Business Card: RW Office Partners - Your organised problem solver

Business Name: RW Office Partners
Website: www.rwofficepartners.com.au
Email: marisol@rwofficepartners.com.au
Mobile: 61 482 907 236
Facebook: @rwofficepartners
Instrgram: @rwofficepartners

Brading Colours:
HEX
#986474
#ddccd3
#7a8498
#c9d8e4
#000000
#ffffff

Tag Line: Your organised problem solver

Link to DRAFT website:
https://deskhelpcollective.wixsite.com/rw-office-partners

About Page from the website:
My name is Marisol Wrenfield, and I would love to assist you to become more productive in your day to day and achieve your business and personal goals.
My mission is to give you time, time to work on the important tasks of your business or to be able to spend more time with your family. I will take on the tasks you don’t have time for, don’t know well or simply don’t like to do.
I have an extensive background in Administration, Tender Coordination, Document Control, WHS and Quality Management working primarily in the Construction, Mining and Corporate World.
I am passionate about being organised, having order and making things in your life (and mine) easier! I love to watch something unfold and grow into something amazing! I am known for being the go-to problem solver, the organiser of all things, producing high standards of work even under pressure. I’m also a confident communicator, and I understand that you’re busy running your business.

Target Market(s)

Small to Medium Business who require assistance in their business by a virtual assistant.

Industry/Entity Type

Virtual Assistant

Contact Information for Business Card

Mobile: 61 482 907 236

Font styles to use
Sans Serif

Colors
ffffff

Requirements
Must have
• Branding Colours as outlined.
Contact Details as outlined.
Logo as provided.
Proper contact details - mobile, facebook, instragm, website.
Simple, Elegant, very clean looking.
Should not have
• Note cute with pictures.
Not too girly as still want to market to construction companies.

```html
<!DOCTYPE html>
<html lang="en">
<head>
<meta charset="utf-8">
<title>RW Office Partners – Business Card</title>
<link href="https://fonts.googleapis.com/css2?family=Exo+2:wght@600&family=Roboto:wght@400&display=swap" rel="stylesheet">
<style>
  :root {
    --mauve: #986474;
    --slate: #7a8498;
    --ink: #2b2b2b;
    --paper: #ffffff;
    --backdrop: #ebe8e9;
  }
  * { margin: 0; padding: 0; box-sizing: border-box; }
  html, body { width: 1200px; height: 1200px; overflow: hidden; }
  body {
    position: relative;
    background: var(--backdrop);
    font-family: "Roboto", Arial, sans-serif;
    color: var(--ink);
  }
  .card {
    position: absolute;
    background: var(--paper);
    border-radius: 28px;
    overflow: hidden;
    box-shadow: 0 2px 6px rgba(0,0,0,0.08);
  }
  .card--front { left: 238px; top: 120px; width: 712px; height: 417px; }
  .card--back  { left: 231px; top: 645px; width: 711px; height: 416px; }

  .brand-name {
    font-family: "Exo 2", Arial, sans-serif;
    font-weight: 600;
    color: var(--mauve);
    white-space: nowrap;
  }
  .front-brand {
    position: absolute;
    left: 0; right: 0; top: 145px;
    text-align: center;
    font-size: 60px;
    line-height: 1;
  }
  .front-social {
    position: absolute;
    left: 0; right: 0; top: 350px;
    display: flex; justify-content: center; gap: 18px;
    font-size: 18px;
  }
  .social-item { display: flex; align-items: center; gap: 9px; }
  .social-mark {
    width: 16px; height: 16px; border-radius: 3px;
    background: var(--mauve); display: inline-block;
  }
  .social-mark--round { border-radius: 50%; background: none; border: 2px solid var(--mauve); }
  .band { position: absolute; bottom: 0; height: 16px; }
  .band--mauve { left: 0; width: 357px; background: var(--mauve); }
  .band--slate { left: 357px; right: 0; background: var(--slate); }

  .holder-name {
    position: absolute; left: 37px; top: 47px;
    font-size: 27px; line-height: 32px;
  }
  .holder-role { position: absolute; left: 37px; top: 82px; font-size: 18px; }
  .back-brand {
    position: absolute; right: 36px; top: 52px;
    font-size: 46px; line-height: 52px; text-align: right;
  }
  .company-name { position: absolute; left: 37px; top: 219px; font-size: 23px; }
  .contact-list {
    position: absolute; left: 37px; top: 256px;
    list-style: none; font-size: 18px;
  }
  .contact-list li { display: flex; align-items: center; height: 26px; }
  .contact-icon { width: 18px; height: 18px; margin-right: 13px; flex: none; }
  .contact-list .social-mark { width: 15px; height: 15px; margin: 0 14px 0 2px; }
  .tagline-band {
    position: absolute; left: 350px; top: 365px;
    width: 361px; height: 51px;
  }
  .tagline {
    position: absolute; left: 419px; top: 377px;
    color: var(--paper); font-size: 18px;
  }
</style>
</head>
<body>
  <section class="card card--front" aria-label="Card front">
    <div class="brand-name front-brand">RW Office Partners</div>
    <div class="front-social">
      <span class="social-item"><span class="social-mark"></span>@rwofficepartners</span>
      <span class="social-item"><span class="social-mark social-mark--round"></span>@rwofficepartners</span>
    </div>
    <div class="band band--mauve"></div>
    <div class="band band--slate"></div>
  </section>

  <section class="card card--back" aria-label="Card back">
    <div class="brand-name holder-name">Marisol Wrenfield</div>
    <div class="holder-role">Virtual Assistant</div>
    <div class="brand-name back-brand">RW Office<br>Partners</div>
    <div class="brand-name company-name">RW Office Partners</div>
    <ul class="contact-list">
      <li>
        <svg class="contact-icon" viewBox="0 0 18 18"><path fill="#986474" d="M2 7c0-2 3-4 7-4s7 2 7 4l-3 1-1-2H6L5 8zM4 9h10l1 6H3z"/><circle cx="9" cy="12" r="1.6" fill="#fff"/></svg>
        61 482 907 236
      </li>
      <li>
        <svg class="contact-icon" viewBox="0 0 18 18"><rect x="1.5" y="4" width="15" height="10" fill="#986474"/><path d="M2 4.5l7 5 7-5M2 13.5l5-4M16 13.5l-5-4" stroke="#fff" stroke-width="1.3" fill="none"/></svg>
        marisol@rwofficepartners.com.au
      </li>
      <li>
        <svg class="contact-icon" viewBox="0 0 18 18" fill="none" stroke="#986474" stroke-width="1.4"><circle cx="9" cy="9" r="7"/><ellipse cx="9" cy="9" rx="3" ry="7"/><path d="M2 9h14M3 5.5h12M3 12.5h12"/></svg>
        www.rwofficepartners.com.au
      </li>
      <li><span class="social-mark"></span>@rwofficepartners</li>
      <li><span class="social-mark social-mark--round"></span>@rwofficepartners</li>
    </ul>
    <svg class="tagline-band" viewBox="0 0 361 51" aria-hidden="true">
      <path d="M28 0H349a12 12 0 0 1 12 12V51H0z" fill="#986474"/>
    </svg>
    <div class="tagline">Your organised problem solver</div>
  </section>
</body>
</html>
```